Vernac Law Business cards and stationary design project

We are looking for a stationary design for business cards (double sided), 8x10, 5x7, and legal and standard envelopes.

We would like the design to match the logo that we have already.
Color palate preferred is Teal, White, grey and any others that will look good for a professional law firm.

We would like this statement: "RELATIONSHIPS. RESPECT. RESULT" to be on the back of the business cards and maybe on the stationary if it looks good.

Please see link to website for more information: www.vernac-law.example

Target Market(s)

Potential clients that need Attorney services.

Industry/Entity Type

Law Firm

Contact Information for Business Card

We would like the front and back to be two different colors. Current business cards are teal front, grey back and are a vertical design. We are open to options with colors.

Font styles to use
Serif

Colors
33a6d7
33b8a4
b9b9b9
5c5c5c

Requirements
Must have
• Logo supplied needs to go on the card and stationary.
• Match website color palate, www.vernac-law.example
• Be professional and not too wordy.
• Criminal Law, Civil Litigation, Personal Injury, Restraining Orders need to be on the card.
Nice to have
• RELATIONSHIPS. RESPECT. RESULTS. on the back of the card.
Should not have
• Not be too busy/wordy or too flashy.

```html
<!DOCTYPE html>
<html lang="en">
<head>
<meta charset="utf-8">
<title>Vernac Law – Business Card</title>
<link rel="stylesheet" href="https://fonts.googleapis.com/css2?family=Cinzel:wght@400;500&family=Tinos&display=swap">
<style>
  :root {
    --backdrop: #3b3b3b;
    --teal: #0e8798;
    --white: #ffffff;
    --card-back: #6f6f6f;
    --ink: #555555;
  }
  * { margin: 0; padding: 0; box-sizing: border-box; }
  html, body { width: 1105px; height: 1200px; overflow: hidden; }
  body { background: var(--backdrop); position: relative; font-family: "Tinos", "Times New Roman", serif; }

  .card { position: absolute; left: 196px; width: 720px; }
  .card-front { top: 146px; height: 412px; background: var(--white); }
  .card-back { top: 602px; height: 410px; background: var(--card-back); color: var(--white); text-align: center; }

  .brand-band { position: absolute; left: 0; top: 0; width: 100%; height: 249px; background: var(--teal); }
  .brand-name {
    position: absolute; left: 32px; width: 240px; top: 140px; text-align: center;
    font-family: "Cinzel", serif; font-weight: 400; font-size: 36px; color: var(--white); letter-spacing: 1px;
  }

  .contact-list { position: absolute; left: 36px; top: 284px; list-style: none; }
  .contact-list li { display: flex; align-items: center; height: 30.5px; font-size: 20px; color: var(--ink); }
  .contact-list svg { width: 18px; height: 18px; margin-right: 15px; fill: var(--teal); flex: none; }

  .person { position: absolute; right: 36px; top: 296px; text-align: right; font-family: "Cinzel", serif; }
  .person-name { font-size: 32px; font-weight: 500; color: var(--teal); letter-spacing: 1px; line-height: 1.1; }
  .person-title { font-size: 21px; color: var(--ink); letter-spacing: 1.5px; margin-top: 4px; }

  .back-name {
    position: absolute; left: 0; width: 100%; top: 168px;
    font-family: "Cinzel", serif; font-weight: 400; font-size: 52px; letter-spacing: 2px;
  }
  .tagline { position: absolute; left: 0; width: 100%; top: 318px; font-family: "Cinzel", serif; font-size: 22px; letter-spacing: 1px; }
  .practice-areas { position: absolute; left: 0; width: 100%; top: 352px; font-size: 21px; }
</style>
</head>
<body>
  <section class="card card-front" aria-label="Business card front">
    <div class="brand-band">
      <div class="brand-name">Vernac Law</div>
    </div>
    <ul class="contact-list">
      <li><svg viewBox="0 0 24 24" aria-hidden="true"><path d="M6.6 10.8a15.1 15.1 0 0 0 6.6 6.6l2.2-2.2c.3-.3.7-.4 1-.2 1.1.4 2.3.6 3.6.6.6 0 1 .4 1 1V20c0 .6-.4 1-1 1A17 17 0 0 1 3 4c0-.6.4-1 1-1h3.5c.6 0 1 .4 1 1 0 1.3.2 2.5.6 3.6.1.3 0 .7-.2 1z"/></svg>(555) 014-2279</li>
      <li><svg viewBox="0 0 24 24" aria-hidden="true"><path d="M2 5h20v14H2z M2 5l10 7 10-7" /><path d="M3 6.2l9 6.3 9-6.3V5H3z" fill="#fff"/></svg>nadia@vernac-law.example</li>
      <li><svg viewBox="0 0 24 24" aria-hidden="true"><circle cx="12" cy="12" r="10"/><path d="M8 6c2 1 1 3 3 3s1 3-1 4-1 4 1 5M15 5c-1 2 1 3 3 3s2 2 2 3" stroke="#fff" stroke-width="1.6" fill="none"/></svg>www.vernac-law.example</li>
    </ul>
    <div class="person">
      <div class="person-name">Nadia Vernac</div>
      <div class="person-title">Trial Lawyer</div>
    </div>
  </section>

  <section class="card card-back" aria-label="Business card back">
    <div class="back-name">Vernac Law</div>
    <div class="tagline">RELATIONSHIPS. RESPECT. RESULTS.</div>
    <div class="practice-areas">Criminal Law,&nbsp; Civil Litigation/Personal Injury, Restraining</div>
  </section>
</body>
</html>
```